wealth management firm, professional group, new model

we have a logo that works but we need a card, white background using our colors...clean look

our tag line if can be used in

The Path From Saver to Steward

```html
<!DOCTYPE html>
<html lang="en">
<head>
<meta charset="utf-8">
<title>Arvela Wealth Partners — Business Card</title>
<link rel="stylesheet" href="https://fonts.googleapis.com/css2?family=Montserrat:wght@400;500;700&display=swap">
<style>
  :root {
    --navy: #14254f;
    --paper: #f3f3f4;
    --backdrop: #d3d3d3;
    --white: #ffffff;
  }
  * { margin: 0; padding: 0; box-sizing: border-box; }
  html, body { width: 1200px; height: 1050px; overflow: hidden; }
  body {
    background: var(--backdrop);
    font-family: "Montserrat", sans-serif;
    color: var(--navy);
    position: relative;
  }
  .card {
    position: absolute;
    width: 600px;
    height: 343px;
    box-shadow: 0 10px 30px rgba(0,0,0,0.18);
  }

  /* Back side */
  .card-back {
    left: 530px;
    top: 120px;
    background: var(--navy);
    color: var(--white);
  }
  .card-back .wordmark {
    position: absolute;
    left: 0; right: 0;
    top: 120px;
    text-align: center;
    font-size: 30px;
    font-weight: 400;
    letter-spacing: 14px;
    padding-left: 14px;
  }
  .tagline-rule {
    position: absolute;
    left: 0; right: 0;
    top: 200px;
    display: flex;
    align-items: center;
    gap: 14px;
  }
  .tagline-rule .rule { flex: 1; height: 1px; background: var(--white); }
  .tagline-rule .tagline {
    font-size: 13px;
    font-weight: 500;
    letter-spacing: 1px;
    white-space: nowrap;
  }

  /* Front side */
  .card-front {
    left: 70px;
    top: 560px;
    background: var(--paper);
    display: flex;
    align-items: center;
    padding: 0 28px 0 32px;
  }
  .brand {
    width: 240px;
    flex: none;
    text-align: center;
  }
  .brand .brand-name {
    font-size: 34px;
    font-weight: 400;
    letter-spacing: 11px;
    padding-left: 11px;
    line-height: 1.1;
  }
  .brand .brand-sub {
    margin-top: 10px;
    font-size: 12px;
    font-weight: 400;
    letter-spacing: 3.2px;
  }
  .divider {
    width: 2px;
    height: 190px;
    flex: none;
    background: var(--navy);
    margin: 0 22px 0 16px;
  }
  .contact { white-space: nowrap; }
  .contact .person {
    font-size: 21px;
    font-weight: 700;
    letter-spacing: 0.2px;
    text-transform: uppercase;
    line-height: 1.2;
  }
  .contact .role {
    font-size: 14px;
    font-weight: 500;
    margin-bottom: 10px;
  }
  .contact .address {
    font-size: 13px;
    font-weight: 500;
    line-height: 1.45;
    margin-bottom: 10px;
  }
  .contact .lines { list-style: none; }
  .contact .lines li {
    display: flex;
    align-items: center;
    gap: 7px;
    font-size: 13px;
    font-weight: 500;
    line-height: 1.55;
  }
  .contact .lines svg { width: 12px; height: 12px; flex: none; }
</style>
</head>
<body>

  <section class="card card-back" aria-label="Card back">
    <div class="wordmark">ARVELA</div>
    <div class="tagline-rule">
      <span class="rule"></span>
      <span class="tagline">The Path From Saver to Steward</span>
      <span class="rule"></span>
    </div>
  </section>

  <section class="card card-front" aria-label="Card front">
    <div class="brand">
      <div class="brand-name">ARVELA</div>
      <div class="brand-sub">WEALTH PARTNERS</div>
    </div>
    <div class="divider"></div>
    <div class="contact">
      <div class="person">Daniel Hartwell</div>
      <div class="role">Advisor</div>
      <div class="address">480 Linden Grove Ave<br>Maple Heights, FL 32000</div>
      <ul class="lines">
        <li>
          <svg viewBox="0 0 24 24" aria-hidden="true"><path fill="var(--navy)" d="M6.6 10.8a15.1 15.1 0 0 0 6.6 6.6l2.2-2.2a1 1 0 0 1 1-.25 11.4 11.4 0 0 0 3.6.57 1 1 0 0 1 1 1V20a1 1 0 0 1-1 1A17 17 0 0 1 3 4a1 1 0 0 1 1-1h3.5a1 1 0 0 1 1 1c0 1.25.2 2.45.57 3.6a1 1 0 0 1-.25 1z"/></svg>
          555-014-2290
        </li>
        <li>
          <svg viewBox="0 0 24 24" aria-hidden="true"><rect x="2" y="5" width="20" height="14" fill="var(--navy)"/><path d="M2 5l10 8 10-8" fill="none" stroke="var(--paper)" stroke-width="2"/></svg>
          hello@arvelawealth.com
        </li>
        <li>
          <svg viewBox="0 0 24 24" aria-hidden="true"><circle cx="12" cy="12" r="10" fill="var(--navy)"/><path d="M2 12h20M12 2c3 3 3 17 0 20M12 2c-3 3-3 17 0 20" fill="none" stroke="var(--paper)" stroke-width="1.4"/></svg>
          arvelawealth.com
        </li>
      </ul>
    </div>
  </section>

</body>
</html>
```